eCommerce website for a DIY shop & communal center

We need a website for a business called The Maple Bench. The Maple Bench is both a shop and communal establishment where people with shared interests, especially in DIY (Do It Yourself) and crafting, can gather to shop for & work on projects while sharing ideas, equipment, supplies and knowledge. The shop is both brick & motor and online. The physical communal space provides workstations, equipment, tools and supplies and expertise for DIY lovers to create their projects.

Target Market(s)

Middle & upper class DIY enthusiasts, creative hobbyists, budding artists & small business owners

Industry/Entity Type

DIY, Arts & Crafts

Coding

Coded - Design and coding required

Number of Pages Required

5+ page

Requirements
Must have
• Menus to include 1. home page (with about us, operating hours, contacts, location, meet the team); 2. Bench activities (how to DIY at the Bench, booking, equipment & tools, house rules); 3. Bench events (events in the Bench, offsite events); 4. Resources (FAQs, tutorials, blogs, eBooks) and 5. Online shop
Nice to have
• Branding guidelines eg logo colours (see attachment) to influence design. Tillpost shop. Booking feature for activities & events at the Bench.

```html
<!DOCTYPE html>
<html lang="en">
<head>
<meta charset="utf-8">
<title>The Maple Bench – Resources</title>
<link href="https://fonts.googleapis.com/css2?family=Roboto:wght@400;500;700&family=Great+Vibes&display=swap" rel="stylesheet">
<style>
:root{
  --ink:#1c1c1c;
  --body:#5a5a5a;
  --line:#d9d9d9;
  --orange:#f2803a;
  --blue:#2f8fd0;
  --pink:#e2457f;
  --slate:#6c7f8c;
  --footer:#0b0b0b;
  --white:#ffffff;
}
*{margin:0;padding:0;box-sizing:border-box}
html,body{width:1123px;height:1200px;overflow:hidden;background:var(--white)}
body{position:relative;font-family:'Roboto',Arial,sans-serif;color:var(--ink)}
.abs{position:absolute}

/* header */
.topbar-rule{left:0;top:46px;width:1123px;height:1px;background:var(--line)}
.phone-badge{left:94px;top:5px;width:35px;height:35px;border:1px solid var(--slate);border-radius:50%;display:flex;align-items:center;justify-content:center}
.phone-number{left:139px;top:13px;font-size:14px;letter-spacing:.3px}
.social-top{top:5px;width:35px;height:35px;border:1px solid var(--slate);border-radius:50%}
.main-nav a{position:absolute;top:59px;font-size:14.5px;color:var(--ink);text-decoration:none;letter-spacing:.2px}
.logo-disc{left:476px;top:-45px;width:170px;height:170px;border-radius:50%;background:var(--white)}
.logo-name{left:476px;top:52px;width:170px;text-align:center;font-weight:700;font-size:17px;color:var(--orange);line-height:1.1}

/* hero */
.hero{left:0;top:94px;width:1123px;height:276px;background:linear-gradient(100deg,#c08a4f 0%,#d9a862 30%,#8a8580 55%,#b7a38a 75%,#7c5a3a 100%)}
.hero-title{left:97px;top:172px;font-size:52px;font-weight:700;color:var(--white);letter-spacing:.5px}

/* faq */
.faq-title{left:0;top:432px;width:1123px;text-align:center;font-family:'Great Vibes',cursive;font-size:44px}
.faq-title .a{color:var(--orange)} .faq-title .b{color:var(--blue)} .faq-title .c{color:var(--pink)}
.agreement{left:95px;top:516px;width:933px;font-size:15.7px;line-height:26.3px;color:var(--body);text-align:justify;text-align-last:center}
.sign-label{top:746px;font-size:18px;font-weight:500}
.sign-line{top:763px;width:169px;height:1px;background:var(--ink)}

/* footer */
.site-footer{left:0;top:853px;width:1123px;height:347px;background:var(--footer)}
.foot-col{top:925px}
.foot-col h4{font-size:16.5px;font-weight:700;color:var(--white);margin-bottom:12px;letter-spacing:.2px}
.foot-col p{font-size:13.5px;color:var(--white);line-height:26.4px}
.email-field{left:789px;top:956px;width:240px;height:40px;border-radius:20px;background:var(--white);font-size:12.5px;padding:13px 14px;color:#333}
.subscribe{left:789px;top:1003px;width:240px;height:40px;border-radius:20px;background:var(--orange);color:var(--white);font-weight:700;font-size:13.5px;text-align:center;line-height:40px}
.social-foot{top:1063px;width:33px;height:33px;border-radius:50%;background:var(--white)}
.foot-rule{left:95px;top:1128px;width:934px;height:1px;background:#333}
.copyright{left:0;top:1144px;width:1123px;text-align:center;font-size:13px;color:var(--white)}
</style>
</head>
<body>

<header>
  <div class="abs phone-badge">
    <svg width="14" height="14" viewBox="0 0 24 24"><path fill="#6c7f8c" d="M6.6 10.8a15.1 15.1 0 0 0 6.6 6.6l2.2-2.2c.3-.3.7-.4 1-.2 1.1.4 2.3.6 3.6.6.6 0 1 .4 1 1V20c0 .6-.4 1-1 1A17 17 0 0 1 3 4c0-.6.4-1 1-1h3.5c.6 0 1 .4 1 1 0 1.2.2 2.4.6 3.6.1.3 0 .7-.2 1l-2.3 2.2z"/></svg>
  </div>
  <div class="abs phone-number">555 - 014 - 2290</div>
  <div class="abs social-top" style="left:870px" aria-label="Social profile"></div>
  <div class="abs social-top" style="left:910px" aria-label="Social profile"></div>
  <div class="abs social-top" style="left:951px" aria-label="Social profile"></div>
  <div class="abs social-top" style="left:992px" aria-label="Social profile"></div>
  <div class="abs topbar-rule"></div>

  <nav class="main-nav">
    <a style="left:94px">HOME</a>
    <a style="left:182px">BENCH ACTIVITIES</a>
    <a style="left:356px">BENCH EVENTS</a>
    <a style="left:658px">RESOURCES</a>
    <a style="left:795px">ONLINE SHOP</a>
    <a style="left:943px">CONTACT US</a>
  </nav>
</header>

<section class="abs hero" role="img" aria-label="Workshop photo of a mitre saw on a plywood workbench"></section>
<div class="abs logo-disc"></div>
<div class="abs logo-name">The Maple<br>Bench</div>
<h1 class="abs hero-title">RESOURCES</h1>

<main>
  <h2 class="abs faq-title"><span class="a">Frequently</span> <span class="b">Asked</span> <span class="c">Questions</span></h2>
  <p class="abs agreement">“Each Party shall hold harmless, and indemnify the other Party and its officers, agents and employees against any and all loss, liability, damage, or expense, including any direct, indirect or consequential loss, liability, damage, or expense, but not including legal fees unless awarded by a court of competent jurisdiction, for injury to persons, and damage to property, including property of either Party, arising out of or in connection with intentional, willful, wanton, reckless or negligent conduct. However, neither Party shall be indemnified hereunder for any loss, liability, damage, or expense resulting from its sole negligence or willful misconduct. Notwithstanding the indemnity provisions contained herein, except for a Party’s willful misconduct or sole negligence, each Party shall be responsible for damage to its own facilities.”</p>

  <div class="abs sign-label" style="left:89px">The Maple Bench</div>
  <div class="abs sign-line" style="left:236px"></div>
  <div class="abs sign-label" style="left:586px">Client with/without supervision</div>
  <div class="abs sign-line" style="left:857px"></div>
</main>

<footer class="abs site-footer"></footer>
<div class="abs foot-col" style="left:95px"><h4>ABOUT</h4><p>Our Story</p><p>Press</p><p>Locations</p><p>Blog</p><p>Contact Us</p></div>
<div class="abs foot-col" style="left:221px"><h4>OUR OFFERING</h4><p>Projects</p><p>Paint Spill Room™</p><p>Parties</p><p>Classes</p></div>
<div class="abs foot-col" style="left:394px"><h4>OTHER</h4><p>Franchise</p><p>Gift Cards</p><p>FAQ</p><p>Refund Policy</p></div>
<div class="abs foot-col" style="left:535px"><h4>CONTACT US</h4><p>78 Timber Lane Brookfield</p><p>40517</p><p>555 - 014 - 2290</p><p>hello@maplebench.com</p></div>
<div class="abs foot-col" style="left:789px"><h4>GET UPDATES &amp; PROMOS</h4></div>
<div class="abs email-field">Email Address</div>
<div class="abs subscribe">SUBSCRIBE</div>
<div class="abs social-foot" style="left:797px" aria-label="Social profile"></div>
<div class="abs social-foot" style="left:836px" aria-label="Social profile"></div>
<div class="abs social-foot" style="left:874px" aria-label="Social profile"></div>
<div class="abs social-foot" style="left:915px" aria-label="Social profile"></div>
<div class="abs foot-rule"></div>
<div class="abs copyright">Copyright © 2021 The Maple Bench. All rights reserved.</div>

</body>
</html>
```